New template needed for Joomla 3.2 website

We are a mortgage origination company based in Johannesburg, South Africa and require a sleek, modern & professional look for our website.
The website is complete and your template should accommodate all pages on the site (there are not many) and be ready for Joomla implementation.
Our website can be viewed at www.keystonebondhub.co.za
Target Market(s)
We are targeting consumers who require mortgage finance to buy real estate. There is no particular demographic, except that we cater to South African home buyers exclusively!
Requirements
Must have
- It must look professional and modern.
Take a look at competitor websites:
www.ziva.co.za
www.pkbondfinder.com
http://www.tallwavegroup.co.za/bondpeak/
http://www.ridgeloan.co.za/
We want to beat the competition !!
Nice to have
- Website should blend with company logo and play on the symbol in the logo.
I want more of a people / photo element to the template. It needs to make us seem "tangible"

```html
<!DOCTYPE html>
<html lang="en">
<head>
<meta charset="utf-8">
<title>Keystone Bond Hub – Home</title>
<link href="https://fonts.googleapis.com/css2?family=Quicksand:wght@500;600;700&family=Open+Sans:wght@400;600&display=swap" rel="stylesheet">
<style>
:root{
  --blue:#0a73ba;
  --blue-light:#1b95dc;
  --blue-dark:#075d99;
  --sky:#3eaee6;
  --ink:#3a3a3a;
  --muted:#8a8a8a;
  --rule:#e2e2e2;
  --footer:#1e1e1e;
  --yellow:#f2c318;
  --page:#ffffff;
  --band:#eeeef2;
}
*{margin:0;padding:0;box-sizing:border-box}
html,body{width:1070px;height:1200px;overflow:hidden;background:var(--page)}
body{position:relative;font-family:"Open Sans",Arial,sans-serif;color:var(--ink)}
.top-band{position:absolute;left:0;top:0;width:1070px;height:318px;background:linear-gradient(#ffffff 0%,#ffffff 35%,var(--band) 100%)}
.site{position:absolute;left:129px;top:0;width:813px;height:1097px}
h1,h2,h3,.nav a,.brand,.phone{font-family:"Quicksand",Arial,sans-serif}

/* header */
.brand{position:absolute;left:4px;top:46px;color:var(--blue-dark);font-weight:700;font-size:28px;line-height:1;white-space:nowrap}
.contact{position:absolute;right:-4px;top:42px;text-align:right}
.contact .label{font-size:14px;color:#777;font-family:"Quicksand",Arial,sans-serif;font-weight:600}
.phone{display:block;margin-top:4px;font-size:22px;font-weight:600;color:var(--blue)}

/* nav */
.nav{position:absolute;left:0;top:103px;width:813px;height:43px;background:linear-gradient(var(--blue-light),var(--blue));border-radius:3px 3px 0 0;display:flex;padding:0 8px}
.nav a{flex:auto;display:flex;align-items:center;justify-content:center;padding:0 8px;height:100%;color:#fff;text-decoration:none;font-size:11.5px;font-weight:700;white-space:nowrap;border-right:1px solid rgba(255,255,255,.22)}
.nav a:last-child{border-right:0}

/* hero */
.hero{position:absolute;left:0;top:146px;width:813px;height:343px;border-radius:0 0 4px 4px;overflow:hidden;background:linear-gradient(100deg,#6c7074 0%,#d9dde1 30%,#f2f3f5 55%,#c9ced4 80%,#eceef1 100%)}
.hero-caption{position:absolute;left:0;top:138px;width:305px;height:92px;background:rgba(20,20,20,.9);border-right:5px solid var(--yellow);padding:17px 0 0 30px}
.hero-caption .kicker{font-family:"Quicksand",Arial,sans-serif;font-weight:600;font-size:21px;color:var(--sky);line-height:1.1}
.hero-caption .headline{font-family:"Quicksand",Arial,sans-serif;font-weight:600;font-size:29px;color:#fff;line-height:1.1}
.hero-dots{position:absolute;left:381px;top:322px;display:flex;gap:4px}
.hero-dots span{width:10px;height:10px;border-radius:50%;background:#1a1a1a}
.hero-dots span:first-child{background:#fff}

/* features */
.feature{position:absolute;top:525px;display:flex}
.feature.free{left:2px;gap:13px}
.feature.service{left:277px;gap:18px}
.feature.credit{left:565px;gap:11px}
.feature-icon{width:60px;height:58px;flex:none;margin-top:10px;border-radius:6px;background:linear-gradient(#c9c9c9,#8e8e8e)}
.feature-icon.badge{border-radius:50%;background:var(--yellow);width:58px}
.feature-icon.card{background:linear-gradient(var(--blue-light),var(--blue-dark));border-radius:10px;width:54px}
.feature h3{font-size:18px;font-weight:600;color:var(--blue);margin-bottom:5px;white-space:nowrap}
.feature p{width:180px;font-size:11.5px;line-height:17.5px;color:var(--muted)}
.btn{display:inline-block;margin-top:12px;width:88px;height:26px;line-height:26px;text-align:center;font-size:10px;font-weight:600;color:#fff;background:linear-gradient(var(--blue-light),var(--blue-dark));border-radius:3px;text-decoration:none}
.divider{position:absolute;left:2px;top:677px;width:807px;height:1px;background:var(--rule)}

/* welcome */
.welcome{position:absolute;left:2px;top:722px;width:545px}
.welcome h1{font-size:24px;font-weight:600;color:#3a3a3a;margin-bottom:10px}
.welcome .lead{font-size:12px;line-height:19px;color:#555;margin-bottom:9px}
.welcome .body{font-size:10.5px;line-height:19px;color:#555}
.promos{position:absolute;left:2px;top:903px;display:flex;gap:18px}
.promo{width:268px;display:flex;gap:10px}
.promo-visual{width:85px;height:66px;flex:none;margin-top:15px;background:linear-gradient(#c99d68,#8e6a40);border-radius:3px}
.promo-visual.cards{background:linear-gradient(135deg,var(--sky),var(--blue-dark));border-radius:6px;margin-top:12px}
.promo h2{font-size:17px;font-weight:600;color:#3a3a3a;line-height:20px;margin-bottom:6px}
.promo p{font-size:10px;line-height:16px;color:var(--muted)}

/* sidebar */
.sidebar{position:absolute;left:570px;top:715px;width:243px;height:322px;border-left:1px solid #ececec;padding:15px 0 0 28px}
.side-item{display:flex;gap:10px;margin-bottom:25px}
.side-item svg{flex:none;margin-top:2px}
.side-item h3{font-size:17px;font-weight:600;color:var(--blue);margin-bottom:4px}
.side-item p{width:150px;font-size:9.5px;line-height:14.5px;color:var(--muted)}

/* footer */
.footer{position:absolute;left:0;top:1097px;width:1070px;height:103px;background:var(--footer)}
.footer-nav{position:absolute;left:132px;top:28px;font-family:"Quicksand",Arial,sans-serif;font-weight:600;font-size:13px;color:#fff;white-space:nowrap}
.footer-nav a{color:#fff;text-decoration:none}
.footer-nav .sep{margin:0 5px}
.copyright{position:absolute;left:132px;top:57px;font-size:10.5px;color:#9a9a9a}
.social{position:absolute;left:858px;top:27px;display:flex;gap:8px}
.social span{width:20px;height:20px;border-radius:2px;background:#3d7fc1}
.social span:nth-child(2){background:#3fa9e0}
.social span:nth-child(3){background:#1c6ea8}
</style>
</head>
<body>
<div class="top-band"></div>

<div class="site">
  <header>
    <div class="brand">Keystone Bond Hub</div>
    <div class="contact">
      <div class="label">Call Us Now!</div>
      <span class="phone">(010) 555 0142</span>
    </div>
  </header>

  <nav class="nav">
    <a href="#">HOME</a>
    <a href="#">ABOUT KEYSTONE</a>
    <a href="#">IMPORTANT INFORMATION</a>
    <a href="#">HOMELOAN CALCULATORS</a>
    <a href="#">APPLY ON-LINE</a>
    <a href="#">CONTACT KEYSTONE</a>
  </nav>

  <section class="hero" role="img" aria-label="Photo of a young couple signing home loan papers with a consultant in a bright office">
    <div class="hero-caption">
      <div class="kicker">FAST HOME LOANS</div>
      <div class="headline">GREAT SERVICES</div>
    </div>
    <div class="hero-dots"><span></span><span></span><span></span><span></span></div>
  </section>

  <article class="feature free">
    <div class="feature-icon" role="img" aria-label="Bank building illustration"></div>
    <div>
      <h3>100% Free of Charge</h3>
      <p>Vestibulum ligula augue bibendum accumsan vestibulum ut commodo a mi Morbi Curabitur iaculis</p>
      <a class="btn" href="#">READ MORE</a>
    </div>
  </article>
  <article class="feature service">
    <div class="feature-icon badge" role="img" aria-label="Satisfaction guarantee seal"></div>
    <div>
      <h3>Exceptional Service</h3>
      <p>Vestibulum ligula augue bibendum accumsan vestibulum ut commodo a mi Morbi Curabitur iaculis</p>
      <a class="btn" href="#">READ MORE</a>
    </div>
  </article>
  <article class="feature credit">
    <div class="feature-icon card" role="img" aria-label="Cut debt card illustration"></div>
    <div>
      <h3>Credit Help</h3>
      <p>Vestibulum ligula augue bibendum accumsan vestibulum ut commodo a mi Morbi Curabitur iaculis</p>
      <a class="btn" href="#">READ MORE</a>
    </div>
  </article>

  <div class="divider"></div>

  <section class="welcome">
    <h1>Welcome to Our Website Mainpage</h1>
    <p class="lead">Donec scelerisque leo ac risus Praesent sit amet est In dictum dolor eu dictum porttitor enim felis viverra mi eget luctus massa purus quis odio Etiam nulla massa</p>
    <p class="body">Aliquam nec erat at purus cursus interdum Vestibulum ligula augue bibendum accumsan vestibulum ut commodo a mi Morbi ornare gravida elit Integer congue augue et malesuada iaculis ipsum dui aliquet felis at cursus magna nisl nec elit Praesent elementum elit at tellus nec ultricies sit amet porttitor mattis enim</p>
  </section>

  <section class="promos">
    <article class="promo">
      <div class="promo-visual" role="img" aria-label="Open cardboard box full of blue balls"></div>
      <div>
        <h2>Keystone Lead<br>Referral Program</h2>
        <p>We invite members of the public, estate agents, attorneys, property developers and all other property professionals to refer leads to us. Why not join our referal</p>
      </div>
    </article>
    <article class="promo">
      <div class="promo-visual cards" role="img" aria-label="Two blue rewards cards"></div>
      <div>
        <h2>Keystone Cash Card</h2>
        <p>All members of our lead referal program will receive an Keystone Homeloans Cash card. We will load money earned from referals to your card</p>
      </div>
    </article>
  </section>

  <aside class="sidebar">
    <div class="side-item">
      <svg width="44" height="44" viewBox="0 0 44 44" aria-hidden="true">
        <rect x="2" y="4" width="40" height="27" rx="2" fill="none" stroke="#0a73ba" stroke-width="3"/>
        <polyline points="7,24 15,16 22,21 30,11 37,15" fill="none" stroke="#0a73ba" stroke-width="2.5"/>
        <rect x="19" y="31" width="6" height="7" fill="#0a73ba"/>
        <rect x="12" y="38" width="20" height="3" fill="#0a73ba"/>
      </svg>
      <div>
        <h3>Referral Program</h3>
        <p>Click on the button below to join our lead referal program and start earning money</p>
      </div>
    </div>
    <div class="side-item">
      <svg width="44" height="44" viewBox="0 0 44 44" aria-hidden="true">
        <rect x="3" y="26" width="6" height="16" fill="#0a73ba"/>
        <rect x="12" y="20" width="6" height="22" fill="#0a73ba"/>
        <rect x="21" y="14" width="6" height="28" fill="#0a73ba"/>
        <rect x="30" y="8" width="6" height="34" fill="#0a73ba"/>
        <polyline points="3,20 17,10 26,4" fill="none" stroke="#0a73ba" stroke-width="3"/>
      </svg>
      <div>
        <h3>Get Pre Qualified</h3>
        <p>Our experienced consultants would be happy to prequalify you for a homeloan.</p>
      </div>
    </div>
    <div class="side-item">
      <svg width="44" height="46" viewBox="0 0 44 46" aria-hidden="true">
        <rect x="8" y="2" width="30" height="42" rx="4" fill="#0a73ba"/>
        <rect x="12" y="6" width="22" height="8" rx="1" fill="#fff"/>
        <g fill="#fff">
          <rect x="12" y="18" width="5" height="5"/><rect x="20" y="18" width="5" height="5"/><rect x="28" y="18" width="5" height="5"/>
          <rect x="12" y="26" width="5" height="5"/><rect x="20" y="26" width="5" height="5"/><rect x="28" y="26" width="5" height="5"/>
          <rect x="12" y="34" width="5" height="5"/><rect x="20" y="34" width="5" height="5"/><rect x="28" y="34" width="5" height="5"/>
        </g>
      </svg>
      <div>
        <h3>Calculators</h3>
        <p>Find out what you can afford with our convenient finance calculators.</p>
      </div>
    </div>
  </aside>
</div>

<footer class="footer">
  <nav class="footer-nav">
    <a href="#">HOME</a><span class="sep">|</span><a href="#">ABOUT KEYSTONE</a><span class="sep">|</span><a href="#">IMPORTANT INFORMATION</a><span class="sep">|</span><a href="#">HOMELOAN CALCULATORS</a><span class="sep">|</span><a href="#">CONTACT US</a>
  </nav>
  <div class="copyright">© 2014 Company Name.&nbsp; All right reserved.&nbsp; Term of Use</div>
  <div class="social" aria-label="Social links"><span></span><span></span><span></span></div>
</footer>
</body>
</html>
```